verdant terraces simple classy business card design

my name is colin barrow and I run a gardening business aimed at high class verdant terraces. the business name is verdant terraces and our logo was designed on pixel harbour .My clientel are anything from residential homes to businesses. I take pride in my work and know that I offer a service like no other in my area.
The business card will be used to represent my business and I want it to be not only rememberable, but simplistic and modern. Eye catching too. Of course I would like it relatable to gardening and appealing to the correct clientel - those being garden enthusiasts, prestigious homes and businesses that are after top of the line gardening services like no other on the market.
I am not a typical lawn mowing business so I don't want a typical card design that represents that. The gardens I work with are generally million dollar properties with owners who are very garden proud looking for upkeep and guidance from me along with sometimes whole new garden designs. I want the business cards to show to my clients that I take pride, as they do, in their garden. And I want them to know from my card that I am a professional, qualified horticulturist offering them a top of the line service for life. I want them to refer my business on. I want them to look at my business card and see class and professionalism in a modern unique bold way.
The card should be simple with the possibility of the logo on the front being embossed/debossed and my details on the back the card should have a organic garden feel it's very important to me that it is absolutely perfect
I am also very open to ideas and suggestions so look forward to seeing the designs. the business logo has been supplied with this project and I want the card to be double sided

Contact info is
Colin Barrow - Managing Director / Horticulturist
Phone : 0481 526 704
Email: colinbarrow@verdantterraces.example.au

Target Market(s)

high class gardens residential and commercial

Industry/Entity Type

Gardener

Contact Information for Business Card

Contact info is
Phone : 0481 526 704

PLEASE MAKE CARD DOUBLE SIDED

Requirements
Must have
• organic simple classy modern feel
• must flow with the current logo that has been supplied with this project
• Double sided
• Must explain in a simple way that I deal with high end gardens and I'm a qualified horticulturist
Nice to have
• embossed debossed logo
Should not have
• shouldn't be to busy or cheap looking

```html
<!DOCTYPE html>
<html lang="en">
<head>
<meta charset="utf-8">
<title>Verdant Terraces – Business Card</title>
<link rel="stylesheet" href="https://fonts.googleapis.com/css2?family=Jost:wght@400;500&display=swap">
<style>
  :root {
    --backdrop: #4b3629;
    --card-stock: #ecebe6;
    --leaf-green: #3f9a3b;
    --card-shadow: rgba(0, 0, 0, 0.35);
  }
  * { box-sizing: border-box; margin: 0; padding: 0; }
  html, body {
    width: 1200px;
    height: 799px;
    overflow: hidden;
    background: var(--backdrop);
    font-family: "Jost", sans-serif;
  }
  .canvas {
    position: relative;
    width: 1200px;
    height: 799px;
  }
  .card {
    position: absolute;
    top: 155px;
    width: 300px;
    height: 490px;
    background: var(--card-stock);
    box-shadow: 0 10px 28px var(--card-shadow);
    color: var(--leaf-green);
    overflow: hidden;
  }
  .card--front { left: 255px; }
  .card--back { left: 645px; }

  /* Front: brand name set along the long edge of the card */
  .front-lockup {
    position: absolute;
    top: 50%;
    left: 50%;
    width: 490px;
    height: 300px;
    transform: translate(-50%, -50%) rotate(90deg);
    display: flex;
    align-items: center;
    justify-content: center;
    gap: 18px;
  }
  .brand-mark {
    width: 58px;
    height: 58px;
    border-radius: 50%;
    background: var(--leaf-green);
    flex-shrink: 0;
  }
  .brand-name {
    font-weight: 500;
    font-size: 30px;
    line-height: 1.15;
    letter-spacing: 0.14em;
    text-transform: uppercase;
  }
  .brand-name span { display: block; }

  /* Back: contact details */
  .back-layout {
    position: absolute;
    inset: 0;
    display: flex;
    flex-direction: column;
    align-items: center;
    text-align: center;
    padding-top: 95px;
  }
  .back-mark {
    width: 120px;
    height: 120px;
    border-radius: 50%;
    background: var(--leaf-green);
    margin-bottom: 48px;
  }
  .holder-name {
    font-weight: 500;
    font-size: 22px;
    letter-spacing: 0.06em;
    text-transform: uppercase;
  }
  .holder-role {
    font-size: 13px;
    margin-top: 2px;
  }
  .contact-list {
    list-style: none;
    margin-top: 20px;
    font-size: 12.5px;
    line-height: 1.55;
  }
</style>
</head>
<body>
  <main class="canvas">
    <section class="card card--front" aria-label="Card front">
      <div class="front-lockup">
        <div class="brand-mark" aria-hidden="true"></div>
        <h1 class="brand-name"><span>Verdant</span><span>Terraces</span></h1>
      </div>
    </section>

    <section class="card card--back" aria-label="Card back">
      <div class="back-layout">
        <div class="back-mark" aria-hidden="true"></div>
        <h2 class="holder-name">Colin Barrow</h2>
        <p class="holder-role">Managing Director/Horticulturist</p>
        <ul class="contact-list">
          <li>0481 526 704</li>
          <li>colinbarrow@verdantterraces.example.au</li>
          <li>verdantterraces.example.au</li>
        </ul>
      </div>
    </section>
  </main>
</body>
</html>
```